Gobal construction supply company needs new business card design

I need a business card design for my global supply company using an existing logo. i will be looking to print these on rounded corner cards with the black background version of my logo on the back. on the front white background, my logo again and my simple details.

```html
<!DOCTYPE html>
<html lang="en">
<head>
<meta charset="utf-8">
<title>Coastal Industrial Supply – Business Card</title>
<link href="https://fonts.googleapis.com/css2?family=Jost:wght@500;600&family=Open+Sans:wght@400;600&display=swap" rel="stylesheet">
<style>
  :root {
    --stage: #8c8c8c;
    --card-white: #f2f2f2;
    --card-black: #1b1b1b;
    --brand-red: #d50000;
    --ink: #1a1a1a;
    --text-grey: #333333;
    --rule: #9a9a9a;
    --white: #ffffff;
  }
  * { margin: 0; padding: 0; box-sizing: border-box; }
  html, body { width: 1200px; height: 1200px; overflow: hidden; }
  body { background: var(--stage); position: relative; font-family: "Open Sans", Arial, sans-serif; }

  .card {
    position: absolute;
    top: 310px;
    width: 366px;
    height: 594px;
    border-radius: 14px;
    overflow: hidden;
  }
  .card--front { left: 233px; background: var(--card-white); text-align: center; }
  .card--back { left: 628px; background: var(--card-black); }

  /* Front */
  .brand {
    position: absolute; top: 178px; left: 0; width: 100%;
    font-family: "Jost", "Futura", sans-serif; font-weight: 600;
    font-size: 24px; line-height: 1.2; color: var(--ink);
    letter-spacing: 0.5px; text-align: center;
  }

  .person { position: absolute; top: 330px; left: 0; width: 100%; }
  .person__name {
    font-family: "Jost", "Futura", sans-serif; font-weight: 500;
    font-size: 27px; color: var(--brand-red); letter-spacing: 0.5px; line-height: 1;
  }
  .person__role { font-size: 17px; color: var(--text-grey); margin-top: 4px; }

  .rule { width: 208px; height: 1px; background: var(--rule); margin: 8px auto; }

  .contact { font-size: 17px; color: var(--text-grey); line-height: 21.5px; }
  .contact__label { color: var(--brand-red); font-weight: 600; }
  .contact__web { color: var(--brand-red); font-weight: 600; }

  .address { font-size: 17px; color: var(--text-grey); line-height: 21px; }

  /* Back */
  .back-band { position: absolute; inset: 0; }
  .back-brand {
    position: absolute; top: 218px; left: 0; width: 100%; text-align: center;
    font-family: "Jost", "Futura", sans-serif; font-weight: 600;
    font-size: 44px; line-height: 1.08; color: var(--white);
  }
  .back-web {
    position: absolute; top: 522px; left: 0; width: 100%; text-align: center;
    font-size: 17px; font-weight: 600; color: var(--brand-red); letter-spacing: 0.6px;
  }
</style>
</head>
<body>

  <section class="card card--front">
    <div class="brand">COASTAL INDUSTRIAL<br>SUPPLY</div>

    <div class="person">
      <div class="person__name">DANIEL HARPER</div>
      <div class="person__role">Managing Director</div>
      <div class="rule"></div>
      <div class="contact">
        <div><span class="contact__label">P:</span> 055-321 654 987</div>
        <div><span class="contact__label">M:</span> 055-321 654 987</div>
        <div><span class="contact__label">E:</span> hello@coastind.com</div>
        <div class="contact__web">www.coastalsupply.com</div>
      </div>
      <div class="rule"></div>
      <div class="address">48 Harbour Road, Unit 5<br>Portland Bay, 302145.</div>
    </div>
  </section>

  <section class="card card--back">
    <svg class="back-band" width="366" height="594" viewBox="0 0 366 594" aria-hidden="true">
      <polygon points="0,0 265,0 0,372" fill="var(--brand-red)"/>
    </svg>
    <div class="back-brand">COASTAL<br>INDUSTRIAL<br>SUPPLY</div>
    <div class="back-web">www.coastalsupply.com</div>
  </section>

</body>
</html>
```